Innovative cost reduction consultant needs to build a group of technical advisors

We need to share our message and compassion for developing cost reduction in the automotive industry. We create opportunities for immediate innovation, by developing cost reduction solutions across suppliers with related process. Attached is an existing Power Point, but it needs improvement. Most of all, a good compelling story, why experts should join us.

Target Market(s)

Automotive industry, supply chain management

Industry/Entity Type

Automotive

Font styles to use
Serif
Sans Serif

Requirements
Must have
• Better visual graphics. There are a few, but they are not as visually appearing as I would like. A graphic with data should have a better visual impact then the ones that I created. I would like to share the message, that I am providing a solution for the automotive industry. The goal is to reduce costs and improve supplier and OEM relationships. The objective is to do so by creating opportunities for immediate innovation, by developing cost reduction solutions across suppliers with related processes. This message may need a visual graphic, which is missing from the presentation.
Nice to have
• Challenge my story and presentation. Does this make sense to you, and what is your opinions of the subject. Or, a relevant news source to validate the story.
Should not have
• I have not decided on the name of the venture or logo. So, let's just use my name as the source or writer. Marcus Delby, Cost Reduction Specialist. Thanks,

```html
<!DOCTYPE html>
<html lang="en">
<head>
<meta charset="utf-8">
<title>Collaborative Effort</title>
<link rel="stylesheet" href="https://fonts.googleapis.com/css2?family=Roboto+Condensed:wght@400;700&display=swap">
<style>
  :root {
    --ink: #333a40;
    --brand-blue: #1a9be0;
    --node-blue: #1e6fc0;
    --panel: #e4e5e6;
    --panel-light: #f4f4f4;
    --line-blue: #3fa9e0;
    --quality: #d81a30;
    --raw: #137682;
    --components: #e8682a;
    --machine: #b4278a;
    --assembly: #4a2e8c;
    --packaging: #178a3c;
    --tooling: #1f78c8;
    --muted: #7b7f83;
  }
  html, body {
    margin: 0;
    padding: 0;
    width: 1200px;
    height: 650px;
    overflow: hidden;
  }
  body {
    position: relative;
    font-family: "Roboto Condensed", "Arial Narrow", sans-serif;
    background: linear-gradient(90deg, #ffffff 0%, #ffffff 62%, #e9eaeb 78%, #cfd1d2 100%);
  }
  .diagram {
    position: absolute;
    left: 0;
    top: 0;
    width: 1200px;
    height: 650px;
  }
  .key-points {
    position: absolute;
    left: 79px;
    top: 38px;
    margin: 0;
    padding: 0;
    list-style: none;
    color: var(--ink);
    font-size: 21px;
    line-height: 34.5px;
  }
  .key-points li {
    position: relative;
    padding-left: 27px;
  }
  .key-points li::before {
    content: "";
    position: absolute;
    left: 0;
    top: 9px;
    border-left: 10px solid var(--brand-blue);
    border-top: 8px solid transparent;
    border-bottom: 8px solid transparent;
  }
  .footer-band {
    position: absolute;
    left: 0;
    bottom: 0;
    width: 1200px;
    height: 26px;
    background: var(--brand-blue);
  }
  .label { fill: #fff; font-family: "Roboto Condensed", "Arial Narrow", sans-serif; text-anchor: middle; }
  .connector { stroke: var(--line-blue); stroke-width: 1.4; stroke-dasharray: 4 3; fill: none; }
  .ring { fill: none; stroke-width: 1.4; stroke-dasharray: 4 3; }
</style>
</head>
<body>

<svg class="diagram" viewBox="0 0 942 510" xmlns="http://www.w3.org/2000/svg" aria-label="Collaborative effort process diagram">
  <defs>
    <linearGradient id="panelFill" x1="0" x2="1" y1="0" y2="0">
      <stop offset="0" stop-color="var(--panel)"/>
      <stop offset="0.75" stop-color="var(--panel)"/>
      <stop offset="1" stop-color="var(--panel-light)"/>
    </linearGradient>
    <radialGradient id="shade" cx="570" cy="330" r="135" gradientUnits="userSpaceOnUse">
      <stop offset="0" stop-color="#fff" stop-opacity="0.18"/>
      <stop offset="1" stop-color="#000" stop-opacity="0.18"/>
    </radialGradient>
    <linearGradient id="wedgeFill" x1="0" x2="1" y1="0" y2="0">
      <stop offset="0" stop-color="#fff" stop-opacity="0.9"/>
      <stop offset="1" stop-color="#fff" stop-opacity="0.5"/>
    </linearGradient>
  </defs>

  <!-- panel -->
  <rect x="57" y="155" width="828" height="297" rx="10" fill="url(#panelFill)"/>

  <!-- common process wedge -->
  <polygon points="688,252 782,192 828,412" fill="url(#wedgeFill)" stroke="#555" stroke-width="1" stroke-dasharray="3 3"/>
  <rect x="782" y="192" width="103" height="46" rx="6" fill="#fff" stroke="#555" stroke-width="1" stroke-dasharray="3 3"/>
  <text x="833" y="211" font-size="17" fill="var(--muted)" text-anchor="middle" font-family="Roboto Condensed, sans-serif">Common</text>
  <text x="833" y="231" font-size="17" fill="var(--muted)" text-anchor="middle" font-family="Roboto Condensed, sans-serif">Process</text>

  <!-- left connectors -->
  <path class="connector" d="M179,248 H195 V326 H179"/>
  <path class="connector" d="M195,287 H222"/>
  <path class="connector" d="M310,287 H333"/>
  <path class="connector" d="M266,265 V253"/>
  <path class="connector" d="M296,253 V262 H398 V253"/>
  <path class="connector" d="M322,262 V287"/>

  <!-- left nodes -->
  <circle cx="152" cy="248" r="27" fill="var(--node-blue)"/>
  <text class="label" x="152" y="252" font-size="12">Forecast</text>
  <circle cx="152" cy="326" r="27" fill="var(--node-blue)"/>
  <text class="label" x="152" y="330" font-size="12">Events</text>

  <rect x="222" y="265" width="88" height="43" rx="4" fill="var(--node-blue)" stroke="#fff" stroke-width="1.5"/>
  <text class="label" x="266" y="283" font-size="14">Servey</text>
  <text class="label" x="266" y="300" font-size="14">data</text>

  <rect x="250" y="208" width="93" height="45" rx="4" fill="var(--node-blue)" stroke="#fff" stroke-width="1.5"/>
  <text class="label" x="296" y="227" font-size="14">Best</text>
  <text class="label" x="296" y="245" font-size="14">practices</text>

  <rect x="353" y="208" width="90" height="45" rx="4" fill="var(--node-blue)" stroke="#fff" stroke-width="1.5"/>
  <text class="label" x="398" y="227" font-size="14">Applied</text>
  <text class="label" x="398" y="245" font-size="14">innovation</text>

  <!-- supplier X,Y,Z -->
  <circle class="ring" cx="386" cy="325" r="60" stroke="var(--line-blue)"/>
  <circle cx="386" cy="325" r="53" fill="var(--node-blue)"/>
  <text class="label" x="388" y="330" font-size="22">Supplier</text>
  <text class="label" x="388" y="357" font-size="22">X,Y,Z</text>

  <!-- area of impact -->
  <path class="connector" d="M630,163 V196" stroke="var(--raw)"/>
  <rect x="608" y="93" width="125" height="70" rx="6" fill="none" stroke="var(--raw)" stroke-width="1.2" stroke-dasharray="3 3"/>
  <rect x="614" y="99" width="113" height="58" rx="3" fill="var(--raw)"/>
  <text x="620" y="117" font-size="15" fill="#fff" font-family="Roboto Condensed, sans-serif">Area of impact</text>
  <text x="620" y="136" font-size="13" fill="#fff" font-family="Roboto Condensed, sans-serif">• Energy</text>
  <text x="620" y="154" font-size="13" fill="#fff" font-family="Roboto Condensed, sans-serif">• Productivity</text>

  <!-- process pie -->
  <g class="process-pie" stroke="#fff" stroke-width="2.5" stroke-linejoin="round" transform="translate(570 330) scale(0.964) translate(-570 -330)">
    <path d="M570,330 L460.5,242.7 A140,140 0 0 1 570,190 Z" fill="var(--quality)"/>
    <path d="M570,330 L433.5,361.2 A140,140 0 0 1 460.5,242.7 Z" fill="var(--tooling)"/>
    <path d="M570,330 L509.3,456.1 A140,140 0 0 1 433.5,361.2 Z" fill="var(--packaging)"/>
    <path d="M570,330 L630.7,456.1 A140,140 0 0 1 509.3,456.1 Z" fill="var(--assembly)"/>
    <path d="M570,330 L706.5,361.2 A140,140 0 0 1 630.7,456.1 Z" fill="var(--machine)"/>
    <path transform="translate(3,-2)" d="M570,330 L679.5,242.7 A140,140 0 0 1 706.5,361.2 Z" fill="var(--components)"/>
    <path transform="translate(4,-9)" d="M570,330 L570,190 A140,140 0 0 1 679.5,242.7 Z" fill="var(--raw)"/>
  </g>
  <circle cx="570" cy="330" r="135" fill="url(#shade)" pointer-events="none"/>

  <text class="label" x="524" y="260" font-size="23">Quality</text>
  <text class="label" x="490" y="331" font-size="22">Tooling</text>
  <text class="label" x="499" y="389" font-size="17">Packaging</text>
  <text class="label" x="569" y="443" font-size="17">Assembly</text>
  <text class="label" x="641" y="383" font-size="17">Machine</text>
  <text class="label" x="639" y="402" font-size="17">process</text>
  <text class="label" x="644" y="335" font-size="17">Components</text>
  <text x="589" y="234" font-size="24" fill="#fff" font-family="Roboto Condensed, sans-serif">Raw</text>
  <text x="589" y="253" font-size="15" fill="#fff" font-family="Roboto Condensed, sans-serif">Materials</text>

  <!-- supplier A,B,G,F -->
  <circle class="ring" cx="756" cy="300" r="59" stroke="var(--components)"/>
  <circle cx="756" cy="300" r="52" fill="var(--components)"/>
  <text class="label" x="756" y="295" font-size="22">Supplier</text>
  <text class="label" x="756" y="322" font-size="22">A,B,G,F</text>

  <!-- title -->
  <rect x="80" y="418" width="345" height="48" rx="8" fill="#fff" stroke="#555" stroke-width="1" stroke-dasharray="3 3"/>
  <text x="252" y="457" font-size="40" font-weight="700" fill="var(--brand-blue)" text-anchor="middle" font-family="Roboto Condensed, sans-serif">Collaborative Effort</text>
</svg>

<ul class="key-points">
  <li>Re–Leveraging the power of a $3B supplier base</li>
  <li>Establishing the maximum effort towards $95M target</li>
  <li>Applying the maximum $23M group effort</li>
  <li>Connect, collaborate, and integrate innovation</li>
</ul>

<div class="footer-band"></div>

</body>
</html>
```